Satchel & Sundial needs new business card design

I need a new business card design. I'm looking for out-of-the-box design which represents the freedom of being a location independent entrepreneur.
I offer coaching, retreats and trips.
I would like to see designs with and without the photo.
Colors I use are black (#000000), green (#25A796) and brown (#D7C38C)
Website satchelandsundial.example

Target Market(s)

location independent entrepreneurs, digital nomads, people looking to swap the 9 to 5 for a lifestyle business

Industry/Entity Type

Business

Contact Information for Business Card

Dorota Falkner
Your Lifestyle Business Coach, Retreat & Trip Leader
http://satchelandsundial.example
hello@satchelandsundial.example
Live a life you don't need a holiday from

Font styles to use
Serif
Sans Serif

Requirements
Must have
• One side should contain only the logo. I would also consider having the "Live a life you don't need a holiday from" on that side too (depending on how it looks)
• Please show both sides on the designs.

```html
<!DOCTYPE html>
<html lang="en">
<head>
<meta charset="utf-8">
<title>Dorota Falkner – Business Card</title>
<link href="https://fonts.googleapis.com/css2?family=Oswald:wght@400;500;600&family=Open+Sans:wght@400&display=swap" rel="stylesheet">
<style>
  :root {
    --ink: #111111;
    --black-band: #161616;
    --green: #25a796;
    --green-dark: #1f8a78;
    --brown: #d7c38c;
    --card: #ece7df;
    --page: #d9d4cc;
    --tagline: #e6e2da;
  }
  * { margin: 0; padding: 0; box-sizing: border-box; }
  html, body {
    width: 1200px; height: 1010px; overflow: hidden;
    background: var(--page);
  }
  .card {
    position: absolute; left: 60px; top: 192px;
    width: 1080px; height: 626px;
    background: var(--card);
    box-shadow: 0 14px 40px rgba(0,0,0,0.18);
    overflow: hidden;
  }
  .card-shapes { position: absolute; inset: 0; width: 100%; height: 100%; }
  .holder-name {
    position: absolute; left: 593px; top: 117px;
    font: 600 37px/1 'Oswald', sans-serif;
    color: var(--ink); letter-spacing: 0.4px; text-transform: uppercase;
    white-space: nowrap;
  }
  .holder-roles {
    position: absolute; left: 593px; top: 164px;
    font: 500 25px/32px 'Oswald', sans-serif;
    color: var(--green-dark); white-space: nowrap;
  }
  .contact-list { position: absolute; left: 593px; top: 302px; list-style: none; }
  .contact-item {
    display: flex; align-items: center; height: 42px;
    font: 400 25px/1 'Oswald', sans-serif; color: var(--ink);
    white-space: nowrap;
  }
  .contact-item--social { margin-top: 5px; }
  .contact-icon { width: 26px; height: 26px; margin-right: 16px; flex: none; }
  .accent { color: var(--green-dark); }
  .social-mark {
    width: 22px; height: 22px; background: var(--ink); border-radius: 4px;
    margin-right: 20px; flex: none;
  }
  .tagline {
    position: absolute; left: 523px; top: 565px;
    font: 400 27px/1.2 'Open Sans', sans-serif;
    color: var(--tagline); letter-spacing: 0.3px; white-space: nowrap;
  }
</style>
</head>
<body>
  <section class="card">
    <svg class="card-shapes" viewBox="0 0 820 475" preserveAspectRatio="none">
      <defs>
        <linearGradient id="photoTone" x1="0" y1="0" x2="1" y2="1">
          <stop offset="0" stop-color="#7d8f5e"/>
          <stop offset="0.5" stop-color="#8f9a72"/>
          <stop offset="1" stop-color="#6b6a4f"/>
        </linearGradient>
        <linearGradient id="goldStrip" x1="0" y1="0" x2="1" y2="0">
          <stop offset="0" stop-color="#c9b27a"/>
          <stop offset="0.5" stop-color="#e3d3a2"/>
          <stop offset="1" stop-color="#b89d62"/>
        </linearGradient>
      </defs>
      <path class="photo-area" role="img" aria-label="Photo of the coach smiling outdoors among pine branches, holding a small sign"
            d="M0 0 H345 C375 90 392 250 362 330 C350 370 340 410 335 440 H0 Z" fill="url(#photoTone)"/>
      <path class="curve-accent" d="M347 0 C378 90 395 250 365 330 C353 370 343 410 338 442"
            fill="none" stroke="var(--green)" stroke-width="9"/>
      <rect class="gold-strip" x="0" y="440" width="340" height="35" fill="url(#goldStrip)"/>
      <polygon class="tagline-band" points="347,413 820,413 820,475 332,475" fill="var(--black-band)"/>
    </svg>

    <h1 class="holder-name">Dorota Falkner</h1>
    <p class="holder-roles">Your Lifestyle Business Coach<br>Retreat &amp; Trip Leader</p>

    <ul class="contact-list">
      <li class="contact-item">
        <svg class="contact-icon" viewBox="0 0 26 26"><rect x="2" y="6" width="22" height="15" fill="var(--green-dark)"/><path d="M2 6 L13 15 L24 6" fill="none" stroke="#fff" stroke-width="2"/></svg>
        hello@satchelandsundial.example
      </li>
      <li class="contact-item">
        <svg class="contact-icon" viewBox="0 0 26 26"><circle cx="13" cy="13" r="10" fill="var(--green-dark)"/><g fill="none" stroke="#fff" stroke-width="1.4"><ellipse cx="13" cy="13" rx="4.5" ry="10"/><line x1="3" y1="13" x2="23" y2="13"/><line x1="5" y1="8" x2="21" y2="8"/><line x1="5" y1="18" x2="21" y2="18"/></g></svg>
        <span>www.<span class="accent">satchelandsundial</span>.example</span>
      </li>
      <li class="contact-item contact-item--social">
        <span class="social-mark"></span>
        <span class="accent">/satchelandsundial</span>
      </li>
    </ul>

    <p class="tagline">Live a life you don't need a holiday from</p>
  </section>
</body>
</html>
```